BUSINESS CARD - HALLORAN FIELD SERVICES

I would like to create a business card for my fertilizer spreading business. I would like to incorporate my existing logo and also a description of the services offered. The business card will be given to farmers so must be kept simple but effective. It will also be left in stores so much also be eye catching in order to stand out from other cards.

Target Market(s)

FARMERS

Requirements
Must have
• FRONT OF CARD = EXISTING LOGO + "CUSTOMISED SPREADING" below the logo

REAR Of CARD = SERVICES OFFERED AND CONTACT DETAILS

- Bulk fertilizer including Lime, Gypsum, Manure & Compost
- Granular fertilizer including Single Super, Urea, Gran-am, & Custom Blends
- Modern equipment - Autosteer & Variable Rate Capable
- Friendly & Reliable Service
- Contact Gus: 0417 552 308
Nice to have
• utilize same color scheme as existing logo

```html
<!DOCTYPE html>
<html lang="en">
<head>
<meta charset="utf-8">
<title>Halloran Field Services – Business Card</title>
<link rel="stylesheet" href="https://fonts.googleapis.com/css2?family=Arimo:wght@400;700&family=Exo+2:wght@700&display=swap">
<style>
  :root {
    --backdrop: #9b9b9b;
    --orange: #f6951f;
    --charcoal: #58585a;
    --paper: #ffffff;
    --ink: #505052;
    --rule: #9a9a9a;
  }
  * { margin: 0; padding: 0; box-sizing: border-box; }
  html, body { width: 1200px; height: 1200px; overflow: hidden; }
  body {
    background: var(--backdrop);
    position: relative;
    font-family: "Arimo", Arial, sans-serif;
  }
  .card {
    position: absolute;
    top: 303px;
    width: 368px;
    height: 594px;
    overflow: hidden;
  }

  /* Front */
  .card--front {
    left: 201px;
    background: linear-gradient(to bottom, var(--orange) 0, var(--orange) 293px, var(--charcoal) 293px);
  }
  .front-mark {
    position: absolute;
    left: 40px;
    top: 140px;
    width: 290px;
    height: 290px;
    border-radius: 50%;
    background: var(--paper);
  }
  .front-brand {
    position: absolute;
    left: 0; right: 0;
    top: 452px;
    text-align: center;
    font-family: "Exo 2", Arial, sans-serif;
    font-weight: 700;
    font-size: 22px;
    letter-spacing: 2px;
    color: var(--paper);
  }
  .front-tagline {
    position: absolute;
    left: 0; right: 0;
    top: 531px;
    text-align: center;
    font-family: "Exo 2", Arial, sans-serif;
    font-weight: 700;
    font-size: 18px;
    letter-spacing: 2.4px;
    color: var(--orange);
  }

  /* Back */
  .card--back {
    left: 600px;
    width: 364px;
    background: var(--paper);
  }
  .back-mark {
    position: absolute;
    left: 50%;
    top: 64px;
    width: 124px;
    height: 124px;
    margin-left: -62px;
    border-radius: 50%;
    background: var(--charcoal);
  }
  .back-brand {
    position: absolute;
    left: 0; right: 0;
    top: 204px;
    text-align: center;
    font-weight: 700;
    font-size: 27px;
    letter-spacing: -0.5px;
    color: var(--ink);
  }
  .services {
    position: absolute;
    left: 0; right: 0;
    top: 306px;
    list-style: none;
    text-align: center;
    font-size: 16.5px;
    line-height: 20.5px;
    color: var(--ink);
  }
  .services li { margin-bottom: 6px; }
  .contact-heading {
    position: absolute;
    left: 0; right: 0;
    top: 504px;
    display: flex;
    justify-content: center;
    align-items: center;
    gap: 8px;
    font-size: 24px;
    color: var(--ink);
  }
  .contact-heading::before,
  .contact-heading::after {
    content: "";
    width: 62px;
    height: 1px;
    background: var(--rule);
  }
  .contact-line {
    position: absolute;
    left: 0; right: 0;
    top: 533px;
    text-align: center;
    font-size: 24px;
    color: var(--ink);
  }
  .contact-line .phone { color: var(--orange); }
</style>
</head>
<body>
  <section class="card card--front">
    <span class="front-mark"></span>
    <p class="front-brand">HALLORAN FIELD SERVICES</p>
    <p class="front-tagline">CUSTOMISED SPREADING</p>
  </section>

  <section class="card card--back">
    <span class="back-mark"></span>
    <h1 class="back-brand">Halloran Field Services</h1>
    <ul class="services">
      <li>Bulk fertilizer including Lime<br>Gypsum, Manure &amp; Compost</li>
      <li>Granular fertilizer including Single<br>Super, Urea, Gran-am, &amp; Custom Blends</li>
      <li>Modern equipment</li>
      <li>Autosteer &amp; Variable Rate Capable</li>
      <li>Friendly &amp; Reliable Service</li>
    </ul>
    <p class="contact-heading">Contact</p>
    <p class="contact-line">Gus: <span class="phone">0417 552 308</span></p>
  </section>
</body>
</html>
```